Stage Design Company Business Card

We are looking to step up up our business card design for our team.

We are a Full service Design and Consultation company for Stage and TV with an emphasis in Theatrical Lighting.

We like our materials to be clean and modern with solid colors free of patterns and gradients. Our brand consists of 4 primary colors Purple, Black, Grey, and White. Provided is our Word Mark as well as our Symbol Logo.

We would like our cards to leave an impression beyond the information, show our attention to design and detail, and make our marks an easily recognized feature (together or apart) for our clients.

We need a warm approachable comfortable feel for some clients, and a professional flair for the board member type clients.

Attached are our brand elements, and our existing cards to give a sense of our style and a glipse at the information we provide on our cards.

Target Market(s)

broad client base from church leaders to high school teachers and architects.

Industry/Entity Type

Business

Contact Information for Business Card

We format our phone number with periods not parenthesis or dashes. Information will be edited for each of our team members, and team member specific cards are not part of this scope, but rather a template so to speak.

Font styles to use
Sans Serif

Colors
6b449b
ffffff
000000
333333
aaaaaa

Requirements
Must have
• Wordmark and logo mark present (does not need to exist on the same side of card)
• Brand Colors,
• Name, Phone, Email, Address.
• Unique choices that make someone stop and take a second look
Nice to have
• It would be nice to somehow convey what we DO, as our brand name does not lend itself to this, outside of an obvious tagline though.....
• social media if not crowded. all of our handles match (instagram, twitter, facebook)
Should not have
• "clipart"

```html
<!DOCTYPE html>
<html lang="en">
<head>
<meta charset="utf-8">
<title>Linden Stageworks — Business Card</title>
<link href="https://fonts.googleapis.com/css2?family=Jost:wght@400;600&display=swap" rel="stylesheet">
<style>
  :root {
    --purple: #3d2370;
    --ink: #333333;
    --grey: #aaaaaa;
    --paper: #ffffff;
    --backdrop: #8e8d8e;
  }
  * { margin: 0; padding: 0; box-sizing: border-box; }
  html, body { width: 1200px; height: 929px; overflow: hidden; }
  body {
    background: var(--backdrop);
    font-family: "Jost", sans-serif;
    position: relative;
  }
  .card {
    position: absolute;
    width: 560px;
    height: 320px;
    background: var(--paper);
    box-shadow: 0 6px 14px rgba(0,0,0,0.35);
    overflow: hidden;
  }
  .card--front { left: 90px; top: 110px; }
  .card--back  { left: 550px; top: 500px; }

  /* Front */
  .brand-lockup {
    position: absolute;
    left: 0; right: 0; top: 118px;
    display: flex;
    flex-direction: column;
    align-items: center;
    gap: 14px;
  }
  .brand-dot {
    width: 46px; height: 46px;
    border-radius: 50%;
    background: var(--purple);
  }
  .brand-name {
    color: var(--purple);
    font-weight: 600;
    font-size: 20px;
    letter-spacing: 0.35em;
    padding-left: 0.35em;
  }

  /* Back */
  .back-brand {
    position: absolute;
    left: 34px; top: 44px;
    display: flex;
    align-items: center;
    gap: 10px;
  }
  .back-brand .brand-dot { width: 30px; height: 30px; }
  .back-brand .brand-name { font-size: 13px; letter-spacing: 0.25em; padding-left: 0; }

  .side-tab {
    position: absolute;
    right: -12px; top: 58px;
    width: 24px; height: 46px;
    border-radius: 12px;
    background: var(--purple);
  }
  .rule {
    position: absolute;
    left: 40px; top: 190px;
    width: 372px; height: 1.5px;
    background: var(--purple);
  }
  .person {
    position: absolute;
    right: 150px; top: 157px;
    color: var(--purple);
    font-weight: 600;
    font-size: 24px;
    letter-spacing: 0.01em;
    line-height: 1;
  }
  .role {
    position: absolute;
    left: 420px; top: 182px;
    color: var(--ink);
    font-size: 13px;
  }
  .address {
    position: absolute;
    left: 425px; top: 214px;
    color: var(--ink);
    font-size: 14px;
    line-height: 1.3;
  }
  .contacts {
    position: absolute;
    left: 40px; top: 202px;
    list-style: none;
    color: var(--ink);
    font-size: 16px;
    line-height: 1.3;
  }
  .contacts li { display: flex; align-items: center; gap: 12px; }
  .contacts svg { width: 12px; height: 12px; flex: none; }
</style>
</head>
<body>
  <section class="card card--front" aria-label="Card front">
    <div class="brand-lockup">
      <span class="brand-dot"></span>
      <span class="brand-name">LINDEN STAGEWORKS</span>
    </div>
  </section>

  <section class="card card--back" aria-label="Card back">
    <div class="back-brand">
      <span class="brand-dot"></span>
      <span class="brand-name">LINDEN STAGEWORKS</span>
    </div>
    <span class="side-tab"></span>
    <h1 class="person">MARA K LINDEN</h1>
    <span class="rule"></span>
    <p class="role">OWNER</p>
    <p class="address">48 N. Birch ST<br>Lakeview, AZ 85299</p>
    <ul class="contacts">
      <li>
        <svg viewBox="0 0 12 12"><rect x="3" y="0.5" width="6" height="11" rx="1" fill="none" stroke="#3d2370" stroke-width="1.2"/></svg>
        800.555.0142
      </li>
      <li>
        <svg viewBox="0 0 12 12"><rect x="0.5" y="2.5" width="11" height="7.5" fill="#3d2370"/><path d="M0.5 2.5 L6 7 L11.5 2.5" fill="none" stroke="#fff" stroke-width="1"/></svg>
        hello@linden-s.com
      </li>
      <li>
        <svg viewBox="0 0 12 12"><circle cx="7" cy="5" r="3.5" fill="none" stroke="#3d2370" stroke-width="1.6"/><path d="M4.5 7.5 L1 11" stroke="#3d2370" stroke-width="2"/></svg>
        linden-s.com
      </li>
    </ul>
  </section>
</body>
</html>
```